CoinHarbor.com Site Redesign

We are looking to redesign our CoinHarbor.com site. This site is focused on helping consumers make smart financial decisions. We provide reviews and articles in various categories.

We are looking for a responsive design to run on wordpress. We will also have adsense advertisements on our page and will want some ad spot space. We are thinking of two column design vs. single column.

Here is an example of what our competitors look like:
ShopperBeacon.org (mostly reviews vs. articles)
Homepage - https://www.shopperbeacon.example/
Category Review Listing - https://www.shopperbeacon.example/mortgage-refinance/best-mortgage-refinance
Individual Review - https://www.shopperbeacon.example/mortgage-refinance/c/loan-orchard-mortgage-refinance-review

- I like that the site is extremely clean. I like the fixed header in mobile

PilotGuide
Homepage - https://www.pilotguide.example/
Category Review Listing-https://www.pilotguide.example/auto_insurance/index.php
Individual Review- https://www.pilotguide.example/auto_insurance/drivora_review.php

Articles - https://www.pilotguide.example/blog/2017/11/20/going-on-a-holiday-road-trip-be-prepared-for-these-hazards/

What I Like? I like the two column layout in that it gives room for advertising.
What I Do NOT Like? The top navigation is a little cumbersome and old. Mobile view is not very good. Content seems a bit cluttered.

PennyMoth
Homepage - https://www.pennymoth.example
Category Review Listing - https://www.pennymoth.example/blog/insurance/best-car-insurance-companies/?trk=pm_gn1_4.0
Individual Review- https://www.pennymoth.example/blog/insurance/veloro-insurance-review/

What I Like? very clean. Like the use of white space and focus on bright color call to action buttons.
What I Do NOT Like? In mobile a lot of content is pushed below the fold because of the large image above the fold. Reviews are not well organized.

Target Market(s)

consumers interested in saving money and making smart financial decisions

Industry/Entity Type

Financial

Logo Text

CoinHarbor.com or CoinHarbor

Coding

Coded - Design and coding required

Number of Pages Required

5+ page

Font styles to use
Sans Serif

Colors

Designer to choose colors to be used in the design.

Requirements
Must have
• -responsive design
• -room for ad space in the right column
Nice to have
• -good use of white space
• -clean layouts
Should not have
• -clutter

```html
<!DOCTYPE html>
<html lang="en">
<head>
<meta charset="utf-8">
<title>CoinHarbor.com – Make smarter financial decisions</title>
<link href="https://fonts.googleapis.com/css2?family=Open+Sans:wght@400;600;700&family=Roboto:wght@400;500;700&display=swap" rel="stylesheet">
<style>
:root{
  --brand:#1b5fae;
  --brand-deep:#0d4a98;
  --accent:#2aa3d8;
  --ink:#2b2b2b;
  --muted:#666;
  --link:#1f6fc0;
  --footer:#4b4f55;
  --white:#fff;
  --line:#d9d9d9;
}
*{margin:0;padding:0;box-sizing:border-box}
html,body{width:1200px;height:2922px;overflow:hidden;background:var(--white)}
body{position:relative;font-family:"Open Sans",Arial,sans-serif;color:var(--ink)}
.abs{position:absolute}

/* header */
.site-header{position:absolute;left:0;top:0;width:1200px;height:88px;background:var(--white)}
.brand{position:absolute;left:99px;top:34px;display:flex;align-items:center;gap:8px;font-family:"Roboto",sans-serif;font-weight:700;font-size:21px;color:var(--brand)}
.brand-mark{width:26px;height:26px;background:var(--brand)}
.register-btn{position:absolute;left:921px;top:14px;width:179px;height:31px;background:var(--accent);color:#fff;font-size:14px;font-weight:600;display:flex;align-items:center;justify-content:center;gap:10px}
.main-nav{position:absolute;right:100px;top:59px;display:flex;gap:28px;font-size:13px;color:#333}
.main-nav .active{color:var(--accent);font-weight:600}

/* hero */
.hero{position:absolute;left:0;top:88px;width:1200px;height:477px;background:linear-gradient(100deg,#3b3530 0%,#7a6c62 35%,#b9b4b0 60%,#5a6f8a 100%)}
.hero-title{position:absolute;top:118px;width:100%;text-align:center;font-family:"Open Sans",sans-serif;font-weight:700;font-size:44px;color:#fff;text-shadow:0 2px 6px rgba(0,0,0,.5)}
.hero-sub{position:absolute;top:184px;width:100%;text-align:center;font-weight:700;font-size:17px;color:#fff;text-shadow:0 1px 4px rgba(0,0,0,.5)}
.hero-search{position:absolute;left:300px;top:255px;width:594px;height:51px;border:3px solid #fff;background:rgba(0,0,0,.35);color:#fff;font-size:18px;padding:13px 18px}
.hero-btn{position:absolute;left:545px;top:323px;width:102px;height:41px;background:var(--accent);color:#fff;font-size:19px;font-weight:600;display:flex;align-items:center;justify-content:center}
.hero-dots{position:absolute;top:436px;left:577px;display:flex;gap:4px}
.hero-dots span{width:10px;height:10px;border-radius:50%;border:2px solid #fff}
.hero-dots span.on{background:#fff}

/* left column */
.section-title{font-family:"Roboto",sans-serif;font-weight:500;font-size:26px;color:#222}
.finder-input{position:absolute;left:99px;top:684px;width:598px;height:52px;border:2px solid #222;font-size:16px;color:#444;padding:14px 18px}
.cat-tile{position:absolute;width:207px;height:142px;display:flex;align-items:center;justify-content:center;font-family:"Roboto",sans-serif;font-weight:500;font-size:19px;color:#fff;text-shadow:0 1px 4px rgba(0,0,0,.8)}
.pager{position:absolute;display:flex;gap:14px}
.pager span{width:30px;height:30px;border-radius:50%;background:var(--brand-deep);display:flex;align-items:center;justify-content:center}

.band{position:absolute;left:0;width:760px;background:linear-gradient(90deg,var(--brand-deep),#2d72c0);color:#fff;text-align:center;box-shadow:0 14px 18px -10px rgba(0,0,0,.35)}
.band h2{font-family:"Open Sans",sans-serif;font-weight:700;font-size:30px;line-height:39px}
.contact-btn{position:absolute;left:341px;top:204px;width:117px;height:39px;background:var(--accent);font-size:16px;font-weight:600;display:flex;align-items:center;justify-content:center}

.article{position:absolute;width:306px}
.article .thumb{width:306px;height:189px}
.article .cat{margin-top:25px;font-family:"Roboto",sans-serif;font-weight:500;font-size:16px;color:var(--link)}
.article h3{margin-top:6px;font-family:"Roboto",sans-serif;font-weight:400;font-size:19px;color:#222}
.article p{margin-top:4px;font-size:12.5px;line-height:19px;color:#555}
.article .meta{margin-top:16px;display:flex;gap:34px;font-size:13px;color:#444}

.feature{position:absolute;width:240px;text-align:center}
.feature .disc{width:100px;height:100px;margin:0 auto;border-radius:50%;background:var(--brand-deep);border:3px solid rgba(255,255,255,.25);display:flex;align-items:center;justify-content:center;box-shadow:0 6px 10px rgba(0,0,0,.3)}
.feature h4{margin-top:16px;font-weight:700;font-size:16px}
.feature p{margin-top:6px;font-size:11px;line-height:15px}

/* right column */
.ad{position:absolute;left:799px;width:301px}
.side-title{position:absolute;left:799px;font-family:"Roboto",sans-serif;font-weight:500}

/* footer */
.site-footer{position:absolute;left:0;top:2560px;width:1200px;height:362px}
.footer-bg{position:absolute;left:0;top:0}
.footer-brand{position:absolute;left:99px;top:87px;display:flex;align-items:center;gap:8px;font-family:"Roboto",sans-serif;font-weight:700;font-size:20px;color:var(--brand)}
.footer-links{position:absolute;top:168px;list-style:none;font-size:12px;line-height:19px;color:#fff}
.newsletter-title{position:absolute;left:824px;top:108px;font-family:"Roboto",sans-serif;font-weight:500;font-size:17px;color:#fff}
.newsletter-input{position:absolute;left:824px;top:150px;width:276px;height:39px;border:2px solid #fff;color:#fff;font-size:12px;padding:10px 8px}
.newsletter-btn{position:absolute;left:824px;top:204px;width:86px;height:26px;background:var(--accent);color:#fff;font-size:13px;font-weight:600;display:flex;align-items:center;justify-content:center}
.social{position:absolute;top:252px;width:27px;height:27px;border-radius:50%;background:#fff}
.footer-rule{position:absolute;left:99px;top:315px;width:1001px;height:1px;background:rgba(255,255,255,.7)}
.copyright{position:absolute;top:331px;width:100%;text-align:center;font-size:11px;color:#fff}
</style>
</head>
<body>

<header class="site-header">
  <div class="brand"><span class="brand-mark"></span>CoinHarbor.com</div>
  <div class="register-btn">
    <svg width="14" height="14" viewBox="0 0 14 14"><circle cx="7" cy="4" r="3.3" fill="#fff"/><path d="M1 14c0-4 3-6 6-6s6 2 6 6z" fill="#fff"/></svg>
    Register / Login
  </div>
  <nav class="main-nav">
    <span class="active">Home</span><span>Annuities</span><span>Auto Insurance</span><span>Credit Monitoring</span><span>Debt Management</span><span>Mortgages</span>
  </nav>
</header>

<section class="hero">
  <div class="abs" style="inset:0" role="img" aria-label="Photo of a financial adviser meeting a smiling young couple at a desk"></div>
  <h1 class="hero-title">Make smarter financial decisions</h1>
  <p class="hero-sub">Find The Best Financial Products &amp; Services</p>
  <div class="hero-search">Glimmer Search</div>
  <div class="hero-btn">Search</div>
  <div class="hero-dots"><span></span><span class="on"></span><span></span><span></span></div>
</section>

<!-- category finder -->
<h2 class="section-title abs" style="left:99px;top:630px">I’m Looking For</h2>
<div class="finder-input">Product Or Categories</div>

<div class="cat-tile" style="left:99px;top:785px;background:linear-gradient(135deg,#3a3a3a,#7a6f66)" role="img" aria-label="Alarm clock photo for annuities">Annuities</div>
<div class="cat-tile" style="left:325px;top:785px;background:linear-gradient(135deg,#8a7c6c,#c9beb2)" role="img" aria-label="Toy car on documents for auto insurance">Auto Insurance</div>
<div class="cat-tile" style="left:551px;top:785px;background:linear-gradient(135deg,#2a2d33,#6d727c)" role="img" aria-label="Laptop photo for credit monitoring">Credit Monitoring</div>
<div class="cat-tile" style="left:99px;top:949px;background:linear-gradient(135deg,#5e6066,#a34a52)" role="img" aria-label="Piggy bank photo for credit repair">Credit Repair</div>
<div class="cat-tile" style="left:325px;top:949px;background:linear-gradient(135deg,#a24a3c,#8aa6c4)" role="img" aria-label="Handshake over a model house for mortgages">Mortgages</div>
<div class="cat-tile" style="left:551px;top:949px;background:linear-gradient(135deg,#4c4f55,#9ba0a8)" role="img" aria-label="Laptop wrapped in chain for identity theft">Identity Theft</div>

<div class="pager" style="left:678px;top:1103px">
  <span><svg width="10" height="12" viewBox="0 0 10 12"><path d="M7 1 2 6l5 5" stroke="#fff" stroke-width="2.4" fill="none"/></svg></span>
  <span><svg width="10" height="12" viewBox="0 0 10 12"><path d="m3 1 5 5-5 5" stroke="#fff" stroke-width="2.4" fill="none"/></svg></span>
</div>

<!-- trust band -->
<section class="band" style="top:1212px;height:317px">
  <h2 style="position:absolute;top:72px;width:100%">Trusted Financial Advice and Reviews<br>Since 2001</h2>
  <p style="position:absolute;top:157px;width:100%;font-size:13px">Disclosure: We receive advertising revenue from some partners. Learn more.</p>
  <div class="contact-btn">Contact Us</div>
</section>

<!-- recent articles -->
<h2 class="section-title abs" style="left:99px;top:1592px">Recent Articles</h2>
<article class="article" style="left:99px;top:1650px">
  <div class="thumb" style="background:linear-gradient(135deg,#dfe8ef,#8ea9c2 60%,#2f3a48)" role="img" aria-label="Hand holding a glowing security shield"></div>
  <div class="cat">Lorem Ipsum</div>
  <h3>Lorem Ipsum Is Simply Dummy</h3>
  <p>Lorem Ipsum is simply dummy text of the printing and typesetting industry. It has been the industry's standard dummy text ever since the 1500s...</p>
  <div class="meta"><span>▦ December 13, 2017</span><span>💬 4, Comments</span></div>
</article>
<article class="article" style="left:454px;top:1650px">
  <div class="thumb" style="background:linear-gradient(135deg,#c7d6e3,#eef2f5 50%,#6b5a4e)" role="img" aria-label="Businesswoman sitting at an office desk"></div>
  <div class="cat">Lorem Ipsum</div>
  <h3>Lorem Ipsum Is Simply Dummy</h3>
  <p>Lorem Ipsum is simply dummy text of the printing and typesetting industry. It has been the industry's standard dummy text ever since the 1500s...</p>
  <div class="meta"><span>▦ December 13, 2017</span><span>💬 4, Comments</span></div>
</article>
<div class="pager" style="left:678px;top:2005px">
  <span><svg width="10" height="12" viewBox="0 0 10 12"><path d="M7 1 2 6l5 5" stroke="#fff" stroke-width="2.4" fill="none"/></svg></span>
  <span><svg width="10" height="12" viewBox="0 0 10 12"><path d="m3 1 5 5-5 5" stroke="#fff" stroke-width="2.4" fill="none"/></svg></span>
</div>

<!-- about band -->
<section class="band" style="top:2110px;height:409px">
  <h2 style="position:absolute;top:60px;width:100%;font-size:25px">What is CoinHarbor.com?</h2>
  <p style="position:absolute;top:103px;width:100%;font-size:15px">Financial Service Advice and Reviews</p>
  <div class="feature" style="left:20px;top:172px">
    <div class="disc"><svg width="44" height="44" viewBox="0 0 44 44"><circle cx="22" cy="13" r="9" fill="#fff"/><path d="M4 42c0-11 8-17 18-17s18 6 18 17z" fill="#fff"/></svg></div>
    <h4>We Analyze &amp; Explain</h4>
    <p>We analyze &amp; explain how each online<br>service works</p>
  </div>
  <div class="feature" style="left:260px;top:172px">
    <div class="disc"><svg width="42" height="46" viewBox="0 0 42 46"><rect x="4" y="3" width="30" height="38" rx="2" fill="none" stroke="#fff" stroke-width="3"/><path d="M10 13h18M10 20h18M10 27h12" stroke="#fff" stroke-width="3"/><path d="m26 40 12-14 3 3-12 14-5 2z" fill="#fff"/></svg></div>
    <h4>We Test &amp; Compare</h4>
    <p>We test &amp; compare the leading<br>services in each category</p>
  </div>
  <div class="feature" style="left:500px;top:172px">
    <div class="disc"><svg width="62" height="14" viewBox="0 0 62 14" fill="#fff"><path id="s" d="M6 0l1.8 4.3 4.6.3-3.5 3 1.1 4.5L6 9.7 2 12.1l1.1-4.5-3.5-3 4.6-.3z"/><use href="#s" x="12.5"/><use href="#s" x="25"/><use href="#s" x="37.5"/><path d="M56 0l1.8 4.3 4.6.3-3.5 3 1.1 4.5L56 9.7l-4 2.4 1.1-4.5-3.5-3 4.6-.3z" fill="none" stroke="#fff" stroke-width="1"/></svg></div>
    <h4>We Review &amp; Rate</h4>
    <p>We review and rate each service to<br>show which is best</p>
  </div>
</section>

<!-- right column -->
<aside>
  <div class="ad" style="top:637px;height:314px;background:linear-gradient(160deg,#2a3fb8,#3a58d8 60%,#6a3fbf)" role="img" aria-label="Advertisement for an affordable business voicemail service"></div>
  <h2 class="side-title" style="top:1028px;font-size:26px;color:#222">Recommended Articles</h2>
  <h3 class="side-title" style="top:1085px;font-size:17px;font-weight:700;color:#222">Our Sponsors</h3>
  <div class="ad" style="top:1147px;height:259px;background:linear-gradient(180deg,#c9a99a,#7b6a66 70%,#c4161c)" role="img" aria-label="Video advertisement for a skin care product"></div>
  <div class="ad" style="top:1482px;height:250px;background:linear-gradient(135deg,#e8ecef,#b9c3cb)" role="img" aria-label="Advertisement for a stock photo service with birds in flight"></div>
  <div class="ad" style="top:1790px;height:659px;background:linear-gradient(180deg,#111,#1b1b1b 70%,#7a2fb0)" role="img" aria-label="Advertisement for a video entertainment streaming service"></div>
</aside>

<!-- footer -->
<footer class="site-footer">
  <svg class="footer-bg" width="1200" height="362" viewBox="0 0 1200 362">
    <defs><linearGradient id="fg" x1="0" y1="0" x2="1" y2="1"><stop offset="0" stop-color="#55595f"/><stop offset="1" stop-color="#3f4348"/></linearGradient></defs>
    <path d="M0 110C300 135 700 60 1200 30V362H0z" fill="url(#fg)"/>
    <path d="M0 118C300 143 700 68 1200 38" stroke="var(--brand-deep)" stroke-width="5" fill="none"/>
    <path d="M0 110C300 135 700 60 1200 30V0H0z" fill="#fff"/>
  </svg>
  <div class="footer-brand"><span class="brand-mark" style="width:24px;height:24px"></span>CoinHarbor.com</div>
  <ul class="footer-links" style="left:101px"><li>About Us</li><li>Privacy policy</li><li>Terms Of Services</li><li>Contact Us</li></ul>
  <ul class="footer-links" style="left:232px;top:160px"><li>Annuities</li><li>Credit Repair</li><li>Identity Theft</li><li>Online Brokerages</li><li>Student Loan Consolidation</li></ul>
  <ul class="footer-links" style="left:409px;top:160px"><li>Auto Insurance</li><li>Debt Management</li><li>Life Insurance</li><li>Payday Loans</li><li>Tax Settlement</li></ul>
  <ul class="footer-links" style="left:530px;top:160px"><li>Credit Monitoring</li><li>Homeowners Insurance</li><li>Mortgages</li><li>Personal Finance</li></ul>
  <ul class="footer-links" style="left:701px;top:155px"><li>Taxes</li><li>Press</li><li>Careers</li><li>Leadership</li><li>Help</li><li>Security</li></ul>
  <h3 class="newsletter-title">Subscribe To Newsletter</h3>
  <div class="newsletter-input">Enter the Email</div>
  <div class="newsletter-btn">Subscribe</div>
  <span class="social" style="left:829px"></span>
  <span class="social" style="left:867px"></span>
  <div class="footer-rule"></div>
  <p class="copyright">Copyright © 2017. All Rights Reserved</p>
</footer>

</body>
</html>
```